Customer Value Leaflet

We need a bi-fold brochure designing, based on the attached PDF wireframes. Our company name is brambleharvik.com (of which the logo is currently being designed). The corporate colour is orange (the exact shade of which we are happy to leave to the designers discretion).

The leaflet will distributed to customer experience experts and marketers so the design needs to be bright, engaging, clean and simple. Design is critical.

It Company

```html
<!DOCTYPE html>
<html lang="en">
<head>
<meta charset="utf-8">
<title>Customer Value Leaflet – brambleharvik.com</title>
<link rel="stylesheet" href="https://fonts.googleapis.com/css2?family=Amatic+SC:wght@400;700&family=Mulish:wght@300;400;600;700&display=swap">
<style>
  :root {
    --backdrop: #e6e6e6;
    --paper: #ffffff;
    --orange: #ee8240;
    --orange-soft: #fbe1d0;
    --orange-blob: rgba(241, 150, 104, 0.62);
    --blue-blob: rgba(150, 200, 228, 0.7);
    --blue-soft: #e1ecf5;
    --blue-text: #2a8fd4;
    --orange-text: #e8803d;
    --ink: #2b2b2b;
    --grey-text: #4a4a4a;
    --fold: #e4e4e4;
  }
  * { box-sizing: border-box; margin: 0; padding: 0; }
  html, body { width: 1200px; height: 799px; overflow: hidden; }
  body {
    background: var(--backdrop);
    font-family: "Mulish", Arial, sans-serif;
    position: relative;
  }
  .spread {
    position: absolute;
    left: 140px; top: 90px;
    width: 920px; height: 620px;
    display: flex;
    background: var(--paper);
    box-shadow: 0 12px 30px rgba(0,0,0,0.12);
  }
  .panel { position: relative; width: 460px; height: 100%; }
  .panel--inner { border-right: 1px solid var(--fold); }

  /* inner panel */
  .intro-bubble {
    position: absolute; left: 34px; top: 40px;
    width: 330px; height: 118px;
    background: var(--orange-soft);
    border-radius: 56px 48px 60px 40px;
    padding: 18px 30px;
    color: var(--orange-text);
    font-size: 17px; font-weight: 300; line-height: 1.25;
    white-space: nowrap;
  }
  .product-name { font-weight: 700; }
  .insight-bubble {
    position: absolute; left: 22px; top: 172px;
    width: 418px; height: 418px;
    background: var(--blue-soft);
    border-radius: 90px 110px 70px 120px;
  }
  .insight-illustration {
    position: absolute; left: 40px; top: 10px;
    width: 350px; height: 190px;
    border-radius: 12px;
    background: linear-gradient(135deg, #cfe2f1 0%, #f6d3bd 60%, #ffffff 100%);
  }
  .insight-text {
    position: absolute; left: 30px; right: 16px; bottom: 34px;
    color: var(--blue-text);
    font-size: 19px; font-weight: 400; line-height: 1.32;
    white-space: nowrap;
  }
  .insight-text strong { font-weight: 700; }

  /* cover panel */
  .brand-tab {
    position: absolute; left: 110px; top: 0;
    width: 240px; height: 82px;
    background: var(--orange);
    border-radius: 0 0 44px 44px;
    display: flex; align-items: center; justify-content: center;
    color: var(--paper);
    font-weight: 700; font-size: 22px;
  }
  .blob { position: absolute; }
  .blob--blue {
    left: 36px; top: 128px; width: 384px; height: 210px;
    background: var(--blue-blob);
    border-radius: 110px 120px 90px 130px;
  }
  .blob--orange {
    left: 150px; top: 290px; width: 290px; height: 200px;
    background: var(--orange-blob);
    border-radius: 100px 90px 110px 80px;
  }
  .tagline-lead {
    position: absolute; left: 70px; top: 170px;
    font-size: 22px; color: var(--ink);
  }
  .tagline-big {
    position: absolute;
    font-family: "Amatic SC", "Comic Sans MS", cursive;
    font-weight: 400;
    color: var(--ink);
    letter-spacing: 4px;
    line-height: 1;
    white-space: nowrap;
  }
  .tagline-big--customer { left: 56px; top: 196px; font-size: 118px; }
  .tagline-big--value { left: 182px; top: 338px; font-size: 128px; letter-spacing: 8px; }
  .tagline-tail {
    position: absolute; left: 330px; top: 500px;
    font-size: 25px; color: var(--grey-text);
  }
</style>
</head>
<body>
  <main class="spread">
    <section class="panel panel--inner">
      <p class="intro-bubble">
        <span class="product-name">LUMAROQ</span> is our Customer<br>Value Platform, designed<br>for Marketers in the Digital<br>Enterprise.
      </p>
      <div class="insight-bubble">
        <div class="insight-illustration" role="img" aria-label="Illustration of a magnifying glass over a line chart, a browser window and test tubes"></div>
        <p class="insight-text">
          <strong>LUMAROQ</strong> is like having a team of<br><strong>data scientists</strong> making valuable<br>insights available to your website in<br>real-time so that you can deliver <strong>the</strong><br><strong>ultimate customer experience</strong>
        </p>
      </div>
    </section>

    <section class="panel panel--cover">
      <div class="brand-tab">brambleharvik</div>
      <div class="blob blob--blue"></div>
      <div class="blob blob--orange"></div>
      <p class="tagline-lead">We’re a</p>
      <h1 class="tagline-big tagline-big--customer">CUSTOMER</h1>
      <h1 class="tagline-big tagline-big--value">VALUE</h1>
      <p class="tagline-tail">Company</p>
    </section>
  </main>
</body>
</html>
```